Bildevold buisnesscard

Hey :) I need a modern buisnesscard for my company Bildevold
It most have:
Dagligleder og Fotograf: Henrik Audun Strandvik

Mob: +4791264085
Epost: post@bildevold.example
Adresse: Kvernbakken9, 6040 Fjordvik

Facbook and instagram logo with text Bildevold

Bildevold logo

It Company

```html
<!DOCTYPE html>
<html lang="no">
<head>
<meta charset="utf-8">
<title>Bildevold – visittkort</title>
<link rel="stylesheet" href="https://fonts.googleapis.com/css2?family=Exo+2:wght@500;700&family=Open+Sans:wght@400&display=swap">
<style>
  :root {
    --backdrop: #555555;
    --card-white: #ffffff;
    --brand-blue: #2a85b9;
    --brand-blue-dark: #1f6f9f;
    --brand-pink: #c9478a;
    --brand-pink-light: #d86aa3;
    --text-light: #ffffff;
  }
  * { margin: 0; padding: 0; box-sizing: border-box; }
  html, body {
    width: 1200px; height: 950px; overflow: hidden;
    background: var(--backdrop);
  }
  .canvas {
    position: relative; width: 1200px; height: 950px;
    display: flex; justify-content: center; align-items: center; gap: 60px;
  }
  .card {
    position: relative; width: 420px; height: 720px; overflow: hidden;
    box-shadow: 0 10px 30px rgba(0,0,0,0.35);
  }
  .card-front { background: var(--card-white); }
  .chevron-band { position: absolute; top: 0; left: 0; width: 420px; height: 300px; }
  .contact-head {
    position: absolute; top: 40px; right: 34px; text-align: right;
    font-family: "Exo 2", sans-serif; color: var(--text-light);
  }
  .person-name { font-size: 25px; font-weight: 700; letter-spacing: 0.5px; }
  .person-role { font-size: 18px; font-weight: 500; margin-top: 8px; }
  .person-phone { font-size: 18px; font-weight: 500; margin-top: 8px; display: flex; justify-content: flex-end; align-items: center; gap: 8px; }
  .person-phone svg { width: 12px; height: 18px; }
  .brand-name {
    font-family: "Exo 2", sans-serif; font-weight: 700;
    color: var(--brand-blue); letter-spacing: 0.5px;
  }
  .front-brand {
    position: absolute; top: 380px; left: 0; width: 100%;
    display: flex; justify-content: center; align-items: center; gap: 14px;
    font-size: 50px;
  }
  .brand-dot { width: 26px; height: 26px; border-radius: 50%; background: var(--brand-pink); }
  .contact-foot {
    position: absolute; bottom: 0; left: 0; width: 100%; height: 220px;
    background: linear-gradient(135deg, var(--brand-pink) 0%, var(--brand-pink-light) 60%, var(--brand-pink) 100%);
    color: var(--text-light); font-family: "Open Sans", sans-serif; font-size: 17px;
    text-align: center; padding-top: 40px; line-height: 1.5;
  }
  .social-row { display: flex; justify-content: center; gap: 12px; margin-top: 18px; }
  .social-dot { width: 24px; height: 24px; border-radius: 50%; background: var(--text-light); }
  .card-back {
    background: var(--brand-pink);
    display: flex; justify-content: center; align-items: center; gap: 16px;
  }
  .card-back .brand-name { color: var(--text-light); font-size: 54px; }
  .card-back .brand-dot { background: var(--text-light); width: 28px; height: 28px; }
</style>
</head>
<body>
<main class="canvas">
  <section class="card card-front">
    <svg class="chevron-band" viewBox="0 0 420 300" aria-hidden="true">
      <defs>
        <linearGradient id="bandBlue" x1="0" y1="0" x2="1" y2="1">
          <stop offset="0" stop-color="#2f90c6"/>
          <stop offset="1" stop-color="#1f6f9f"/>
        </linearGradient>
      </defs>
      <polygon points="0,0 420,0 420,215 210,300 0,215" fill="url(#bandBlue)"/>
    </svg>
    <div class="contact-head">
      <p class="person-name">Henrik Audun Strandvik</p>
      <p class="person-role">Dagligleder og Fotograf</p>
      <p class="person-phone">
        <svg viewBox="0 0 12 18" aria-hidden="true"><rect x="1" y="1" width="10" height="16" rx="2" fill="none" stroke="#fff" stroke-width="1.5"/><circle cx="6" cy="14.5" r="1" fill="#fff"/></svg>
        +4791264085
      </p>
    </div>
    <div class="front-brand">
      <span class="brand-dot" aria-hidden="true"></span>
      <span class="brand-name">Bildevold</span>
    </div>
    <div class="contact-foot">
      <p>post@bildevold.example</p>
      <p>Kvernbakken9, 6040 Fjordvik</p>
      <p>www.bildevold.example</p>
      <div class="social-row">
        <span class="social-dot" role="img" aria-label="Sosiale medier"></span>
        <span class="social-dot" role="img" aria-label="Sosiale medier"></span>
      </div>
    </div>
  </section>
  <section class="card card-back">
    <span class="brand-name">Bildevold</span>
    <span class="brand-dot" aria-hidden="true"></span>
  </section>
</main>
</body>
</html>
```